ecommerce news podcast artwork

Podcast cover art for a podcast featuring daily news and events around ecommerce product businesses.

text to be: BRISK LOOP
optional third line of text with smaller font: Podcast

looking for something that pops with a medium to light blue background. text can be in white/red/orange colors. prefer solid colors for text, but background can vary.
I'm really open to other ideas too, sometimes you don't know what you want until you see it.

Target Market(s)

ecommerce business owners, managers

Industry/Entity Type

news, business, ecommerce

Font styles to use
Sans Serif

Colors
0054AA
0677BA
7BADD7
CADEEF
E8F1F8
0094D4
00A9DD
6FCCEA
C7EBF8
E9F6FB
F0912C
F2A743
F7CA91
FBE8D2
FDF5EE
EB3D1F
EC4F4E
F09395
F8D3D4
FCEDEE

Requirements
Must have
• text: BRISK LOOP
Should not have
• no microphones, headsets/headphones, speakers, or other props like that.

```html
<!DOCTYPE html>
<html lang="en">
<head>
<meta charset="utf-8">
<title>Brisk Loop Podcast Cover</title>
<link rel="stylesheet" href="https://fonts.googleapis.com/css2?family=Anton&family=Rubik:wght@900&family=Montserrat:wght@400&display=swap">
<style>
  :root {
    --sky-center: #dafbfd;
    --sky-mid: #c4f1fa;
    --sky-edge: #8ccbe6;
    --headline-red: #f70a0a;
    --badge-orange: #f4790c;
    --badge-shade: #c95a05;
    --loop-white: #ffffff;
    --cart-tone: #f2a98a;
    --bag-tone: #f6b533;
  }
  html, body {
    margin: 0;
    padding: 0;
    width: 1200px;
    height: 1200px;
    overflow: hidden;
    background: var(--sky-mid);
  }
  .cover {
    display: block;
    width: 1200px;
    height: 1200px;
  }
  .title-brisk {
    font-family: "Anton", sans-serif;
    fill: var(--headline-red);
  }
  .title-loop {
    font-family: "Rubik", sans-serif;
    font-weight: 900;
    fill: var(--loop-white);
  }
  .title-loop-shade {
    font-family: "Rubik", sans-serif;
    font-weight: 900;
    fill: var(--badge-shade);
  }
  .subtitle {
    font-family: "Montserrat", sans-serif;
    font-weight: 400;
    fill: var(--headline-red);
    letter-spacing: 6px;
  }
  .signal-wave {
    fill: none;
    stroke: var(--headline-red);
    stroke-width: 6;
    stroke-linecap: round;
  }
</style>
</head>
<body>
<svg class="cover" viewBox="0 0 1200 1200" xmlns="http://www.w3.org/2000/svg">
  <defs>
    <radialGradient id="sky" cx="50%" cy="55%" r="75%">
      <stop offset="0" stop-color="var(--sky-center)"/>
      <stop offset="0.55" stop-color="var(--sky-mid)"/>
      <stop offset="1" stop-color="var(--sky-edge)"/>
    </radialGradient>
  </defs>

  <rect class="backdrop" width="1200" height="1200" fill="url(#sky)"/>

  <text class="title-brisk" x="193" y="508" font-size="370" textLength="845" lengthAdjust="spacingAndGlyphs">BRISK</text>

  <rect class="title-badge" x="194" y="540" width="844" height="335" rx="24" fill="var(--badge-orange)"/>

  <text class="title-loop-shade" x="252" y="840" font-size="357" textLength="744" lengthAdjust="spacingAndGlyphs">LOOP</text>
  <text class="title-loop" x="245" y="834" font-size="357" textLength="744" lengthAdjust="spacingAndGlyphs">LOOP</text>

  <rect class="cart-illustration" x="81" y="672" width="164" height="244" rx="18" fill="var(--cart-tone)" opacity="0.85" role="img" aria-label="Shopping cart holding shopping bags"/>
  <rect class="bags-illustration" x="960" y="729" width="163" height="187" rx="18" fill="var(--bag-tone)" role="img" aria-label="Two yellow shopping bags"/>

  <g class="broadcast-left">
    <path class="signal-wave" d="M380 918 Q370 937 380 956"/>
    <path class="signal-wave" d="M364 908 Q350 937 364 966"/>
    <path class="signal-wave" d="M348 898 Q330 937 348 976"/>
  </g>
  <text class="subtitle" x="404" y="965" font-size="80" textLength="422" lengthAdjust="spacingAndGlyphs">PODCAST</text>
  <g class="broadcast-right">
    <path class="signal-wave" d="M846 918 Q856 937 846 956"/>
    <path class="signal-wave" d="M862 908 Q876 937 862 966"/>
    <path class="signal-wave" d="M878 898 Q896 937 878 976"/>
  </g>
</svg>
</body>
</html>
```